Ridgeline Haul Carriers - Website

A clean, not cluttered informative website for our business. We specialize in the transportation of radioactive materials across North America. The site is mostly for information about our company and will not be used to attract business but will be used to attract employee's mainly drivers. Driver's are very hard to find in our area. One of the pages needs to be a job's posting page with an apply now button. Either an application can be filled out there or a resume can be uploaded which ever functionality works better. I would like a website that I can easily edit, ability to change text and photos.

Number of Pages Required

5+ page

Colors

Designer to choose colors to be used in the design.

Requirements
Must have
• Home - About - Services - Jobs - Contact pages
• A way prospective employee's can apply or upload their resume to be emailed to me
• Very clean apperance
Should not have
• I don't want it to be busy

```html
<!DOCTYPE html>
<html lang="en">
<head>
<meta charset="utf-8">
<title>Ridgeline Haul Carriers</title>
<link href="https://fonts.googleapis.com/css2?family=Orbitron:wght@600;700;800&family=Jost:wght@400;500;600&display=swap" rel="stylesheet">
<style>
:root{
  --red:#e01b22;
  --grey:#8a8a8a;
  --ink:#222;
  --text:#444;
  --white:#fff;
  --btn:#8c8c8c;
  --footer:#222224;
  --bar:#111;
}
*{box-sizing:border-box;margin:0;padding:0}
html,body{width:1200px;height:3041px;overflow:hidden}
body{font-family:"Jost",sans-serif;color:var(--text);background:var(--white);position:relative}
.wide{font-family:"Orbitron",sans-serif;font-weight:800;text-transform:uppercase;letter-spacing:2px}

.site-header{position:absolute;top:0;left:0;width:1200px;height:106px;background:var(--white);border-top:3px solid var(--red)}
.brand{position:absolute;left:140px;top:34px;display:flex;align-items:center;gap:10px}
.brand-dot{width:16px;height:16px;background:var(--red);border-radius:50%}
.brand-name{font-weight:600;font-size:26px;color:var(--red);letter-spacing:.5px}
.top-phone{position:absolute;right:144px;top:16px;font-size:18px;font-weight:500;color:var(--grey);letter-spacing:1px;display:flex;align-items:center;gap:10px}
.main-nav{position:absolute;right:144px;top:62px;display:flex;gap:56px}
.main-nav a{font-family:"Orbitron",sans-serif;font-weight:700;font-size:12px;color:var(--grey);text-decoration:none;letter-spacing:1.5px;padding-bottom:10px}
.main-nav a.active{color:var(--red);border-bottom:2px solid var(--red)}

.hero{position:absolute;top:106px;left:0;width:1200px;height:574px;background:linear-gradient(100deg,#3a3a3c 0%,#5a3030 22%,#4a4a4c 50%,#6a5a50 75%,#2e2e30 100%)}
.hero::after{content:"";position:absolute;inset:0;background:rgba(0,0,0,.35)}
.hero-content{position:absolute;top:205px;left:0;width:1200px;text-align:center;z-index:1}
.hero h1{font-weight:500;font-size:36px;line-height:55px;color:var(--white)}
.btn{display:inline-flex;align-items:center;gap:14px;height:36px;padding:0 5px 0 18px;border-radius:18px;color:var(--white);font-size:14px;background:var(--btn);text-decoration:none}
.btn .arrow{width:26px;height:26px;border-radius:50%;background:var(--white);display:flex;align-items:center;justify-content:center}
.btn-red{background:var(--red)}
.hero .btn{margin-top:16px}
.dots{position:absolute;bottom:30px;left:0;width:1200px;display:flex;justify-content:center;gap:8px;z-index:1}
.dots span{width:12px;height:12px;border-radius:50%;background:#999}
.dots span.on{background:var(--red);border:2px solid #fff}

.about{position:absolute;top:680px;left:0;width:1200px;height:415px;text-align:center}
.section-title{font-size:26px;color:var(--grey);letter-spacing:2px}
.section-title b{color:var(--red);font-weight:800}
.about .section-title{margin-top:76px}
.rule{width:260px;height:1px;background:#999;margin:16px auto 0}
.about .lead{width:880px;margin:26px auto 0;font-size:16px;line-height:25px;color:var(--ink)}
.about .small{width:860px;margin:16px auto 0;font-size:11.5px;line-height:19px;color:#555}
.about .btn{margin-top:22px}

.panels{position:absolute;top:1095px;left:0;width:1200px;height:1145px;background:linear-gradient(180deg,#3c3c3e 0%,#555658 40%,#3a3a3c 70%,#2a2a2c 100%)}
.panels::after{content:"";position:absolute;inset:0;background:rgba(0,0,0,.3)}
.panel-title{position:absolute;left:0;width:1200px;text-align:center;font-size:28px;color:var(--white);letter-spacing:3px;z-index:1}
.card{position:absolute;left:142px;width:918px;height:368px;background:var(--white);border-radius:4px;display:flex;overflow:hidden;z-index:1}
.card .photo{width:458px;height:100%}
.card .body{flex:1;padding:32px 34px}
.card h3{color:var(--red);font-weight:500;font-size:18px;margin-bottom:14px}
.card p{font-size:12.5px;line-height:19px;color:#444;margin-bottom:10px}
.card p.strong{color:var(--ink);font-weight:500;font-size:12.5px;white-space:nowrap}
.ticks{list-style:none;margin:4px 0 18px}
.ticks li{font-size:12.5px;line-height:20.5px;color:#444;display:flex;align-items:center;gap:10px}

.cta{position:absolute;top:2240px;left:0;width:1200px;height:335px;text-align:center}
.cta h2{margin-top:84px;font-size:27px;line-height:46px;color:var(--grey);letter-spacing:3px}
.cta h2 b{color:var(--red);font-weight:800}
.cta .btn{margin-top:36px}

.site-footer{position:absolute;top:2575px;left:0;width:1200px;height:466px;background:linear-gradient(180deg,#ffffff 0,#ffffff 20px,#3a3a3c 90px,var(--footer) 160px);overflow:hidden}
.footer-scene{position:absolute;left:0;top:30px;width:520px;height:394px;background:linear-gradient(180deg,#6c7884 0%,#4e5a64 50%,#2c2e32 100%)}
.footer-nav{position:absolute;left:525px;top:147px;display:flex;gap:34px;font-family:"Orbitron",sans-serif;font-weight:700;font-size:10px;letter-spacing:1px}
.footer-nav a{color:var(--white);text-decoration:none}
.footer-nav a.active{color:var(--red)}
.footer-head{position:absolute;top:212px;font-family:"Orbitron",sans-serif;font-weight:700;font-size:11px;color:var(--white);letter-spacing:1.5px;text-transform:uppercase}
.footer-head::after{content:"";display:block;width:40px;height:1px;background:#888;margin-top:10px}
.contact-list{position:absolute;left:533px;top:252px;list-style:none}
.contact-list li{display:flex;gap:16px;font-size:11px;line-height:16px;color:#ccc;margin-bottom:22px}
.map{position:absolute;left:858px;top:255px;width:200px;height:125px;background:linear-gradient(135deg,#e8ece4,#d6e0d0);border-radius:2px}
.footer-bar{position:absolute;left:0;bottom:0;width:1200px;height:42px;background:var(--bar);display:flex;align-items:center}
.copyright{position:absolute;left:520px;font-size:11px;color:#bbb}
.social{position:absolute;right:140px;display:flex;gap:16px}
.social span{width:12px;height:12px;border-radius:50%;background:var(--white)}
</style>
</head>
<body>

<header class="site-header">
  <div class="brand"><span class="brand-dot"></span><span class="brand-name">Ridgeline Haul Carriers</span></div>
  <div class="top-phone">
    <svg width="16" height="16" viewBox="0 0 24 24"><path fill="#e01b22" d="M6.6 10.8a15 15 0 0 0 6.6 6.6l2.2-2.2c.3-.3.7-.4 1-.2 1.1.4 2.3.6 3.6.6.6 0 1 .4 1 1V20c0 .6-.4 1-1 1A17 17 0 0 1 3 4c0-.6.4-1 1-1h3.5c.6 0 1 .4 1 1 0 1.3.2 2.5.6 3.6.1.3 0 .7-.2 1z"/></svg>
    555-014-2290
  </div>
  <nav class="main-nav">
    <a class="active">HOME</a><a>ABOUT</a><a>SERVICES</a><a>JOBS</a><a>CONTACT</a>
  </nav>
</header>

<section class="hero" role="img" aria-label="Red semi truck hauling a flatbed trailer">
  <div class="hero-content">
    <h1>Specializing in the Transportation of Radioactive<br>Materials Across North America</h1>
    <a class="btn btn-red">Contact Us Today <span class="arrow"><svg width="12" height="10" viewBox="0 0 12 10"><path d="M1 1l4 4-4 4M6 1l4 4-4 4" stroke="#e01b22" stroke-width="1.6" fill="none"/></svg></span></a>
  </div>
  <div class="dots"><span class="on"></span><span></span><span></span></div>
</section>

<section class="about">
  <h2 class="section-title wide"><b>About Ridgeline</b> Haul Carriers</h2>
  <div class="rule"></div>
  <p class="lead">Lorem ipsum dolor sit amet, consectetuer adipiscing elit, sed diam nonummy nibh euismod tincidunt ut laoreet dolore magna aliquam erat volutpat. Ut wisi enim ad minim veniam, quis nostrud exerci tation</p>
  <p class="small">suscipit lobortis nisl ut aliquip ex ea commodo consequat. Duis autem vel eum iriure dolor in hendrerit in vulputate velit esse molestie consequat, vel illum dolore eu feugiat nulla facilisis at vero eros et accumsan et iusto odio dignissim qui blandit praesent luptatum zzril delenit augue duis dolore te feugait nulla facilisi. elit, sed diam nonummy nibh euismod tincidunt ut laoreet dolore magna aliquam erat volutpat. Ut wisi enim ad minim veniam,</p>
  <a class="btn">Read More <span class="arrow"><svg width="12" height="10" viewBox="0 0 12 10"><path d="M1 1l4 4-4 4M6 1l4 4-4 4" stroke="#8c8c8c" stroke-width="1.6" fill="none"/></svg></span></a>
</section>

<section class="panels" role="img" aria-label="Row of parked white truck cabs, blurred">
  <h2 class="panel-title wide" style="top:68px">Service We Provide</h2>
  <article class="card" style="top:150px">
    <div class="photo" role="img" aria-label="Flatbed truck carrying yellow transport casks" style="background:linear-gradient(180deg,#7fa3c9 0%,#a9c0d6 45%,#8a8270 70%,#6e6450 100%)"></div>
    <div class="body">
      <h3>Transportation of Radioactive Materials</h3>
      <p>Lorem ipsum dolor sit amet, consectetuer adipiscing elit, sed diam no nummy nibh euismod tincidunt ut laoreet dolore magna</p>
      <p>Lorem ipsum dolor sit amet, consectetuer adipiscing elit, sed diamnomy nibh euismod tincidunt ut laoreet dolore magna suscipit lobortis nisl ut aliquip ex ea commodo consequat.</p>
      <ul class="ticks">
        <li><svg width="12" height="12" viewBox="0 0 12 12"><rect x=".5" y=".5" width="11" height="11" fill="none" stroke="#e01b22"/><path d="M3 6l2 2 4-5" stroke="#e01b22" stroke-width="1.6" fill="none"/></svg>injected humour</li>
        <li><svg width="12" height="12" viewBox="0 0 12 12"><rect x=".5" y=".5" width="11" height="11" fill="none" stroke="#e01b22"/><path d="M3 6l2 2 4-5" stroke="#e01b22" stroke-width="1.6" fill="none"/></svg>true generator on the Internet</li>
        <li><svg width="12" height="12" viewBox="0 0 12 12"><rect x=".5" y=".5" width="11" height="11" fill="none" stroke="#e01b22"/><path d="M3 6l2 2 4-5" stroke="#e01b22" stroke-width="1.6" fill="none"/></svg>Lorem Ipsum generators</li>
        <li><svg width="12" height="12" viewBox="0 0 12 12"><rect x=".5" y=".5" width="11" height="11" fill="none" stroke="#e01b22"/><path d="M3 6l2 2 4-5" stroke="#e01b22" stroke-width="1.6" fill="none"/></svg>Many desktop publishing packages</li>
      </ul>
      <a class="btn">Know More <span class="arrow"><svg width="12" height="10" viewBox="0 0 12 10"><path d="M1 1l4 4-4 4M6 1l4 4-4 4" stroke="#8c8c8c" stroke-width="1.6" fill="none"/></svg></span></a>
    </div>
  </article>

  <h2 class="panel-title wide" style="top:592px">Join Our Team</h2>
  <article class="card" style="top:675px">
    <div class="body">
      <h3>Driving Opportunities</h3>
      <p>Lorem ipsum dolor sit amet, consectetuer adipiscing elit, sed diammony nibh euismod tincidunt ut laoreet.</p>
      <p class="strong">To speak with the Driver Recruiting Department, call 555.014.2290</p>
      <ul class="ticks">
        <li><svg width="12" height="12" viewBox="0 0 12 12"><rect x=".5" y=".5" width="11" height="11" fill="none" stroke="#e01b22"/><path d="M3 6l2 2 4-5" stroke="#e01b22" stroke-width="1.6" fill="none"/></svg>Drivers Apply Online</li>
        <li><svg width="12" height="12" viewBox="0 0 12 12"><rect x=".5" y=".5" width="11" height="11" fill="none" stroke="#e01b22"/><path d="M3 6l2 2 4-5" stroke="#e01b22" stroke-width="1.6" fill="none"/></svg>Drivers Benefits</li>
        <li><svg width="12" height="12" viewBox="0 0 12 12"><rect x=".5" y=".5" width="11" height="11" fill="none" stroke="#e01b22"/><path d="M3 6l2 2 4-5" stroke="#e01b22" stroke-width="1.6" fill="none"/></svg>Driving Career Path</li>
        <li><svg width="12" height="12" viewBox="0 0 12 12"><rect x=".5" y=".5" width="11" height="11" fill="none" stroke="#e01b22"/><path d="M3 6l2 2 4-5" stroke="#e01b22" stroke-width="1.6" fill="none"/></svg>Drivers Frequently Asked Questions</li>
        <li><svg width="12" height="12" viewBox="0 0 12 12"><rect x=".5" y=".5" width="11" height="11" fill="none" stroke="#e01b22"/><path d="M3 6l2 2 4-5" stroke="#e01b22" stroke-width="1.6" fill="none"/></svg>Drivers Incentive Programs</li>
        <li><svg width="12" height="12" viewBox="0 0 12 12"><rect x=".5" y=".5" width="11" height="11" fill="none" stroke="#e01b22"/><path d="M3 6l2 2 4-5" stroke="#e01b22" stroke-width="1.6" fill="none"/></svg>Paid Apprenticeship CDL Training</li>
      </ul>
      <a class="btn">Apply Now <span class="arrow"><svg width="12" height="10" viewBox="0 0 12 10"><path d="M1 1l4 4-4 4M6 1l4 4-4 4" stroke="#8c8c8c" stroke-width="1.6" fill="none"/></svg></span></a>
    </div>
    <div class="photo" role="img" aria-label="Driver leaning from the window of a white truck cab" style="width:464px;background:linear-gradient(160deg,#4f86c6 0%,#8fb5de 35%,#dcdcdc 60%,#9a9a9a 100%)"></div>
  </article>
</section>

<section class="cta">
  <h2 class="wide"><b>Lorem Ipsum</b> Dolor Sit Amet Cidunt Ut<br>Magna Aliquam Erat Volutpat</h2>
  <a class="btn">Contact Us Today <span class="arrow"><svg width="12" height="10" viewBox="0 0 12 10"><path d="M1 1l4 4-4 4M6 1l4 4-4 4" stroke="#8c8c8c" stroke-width="1.6" fill="none"/></svg></span></a>
</section>

<footer class="site-footer">
  <div class="footer-scene" role="img" aria-label="Curving road sweeping over a waterfront city skyline"></div>
  <nav class="footer-nav"><a class="active">• HOME</a><a>• ABOUT</a><a>• SERVICES</a><a>• JOBS</a><a>• CONTACT</a></nav>
  <div class="footer-head" style="left:533px">Contact Details</div>
  <div class="footer-head" style="left:858px">Location Map</div>
  <ul class="contact-list">
    <li><svg width="10" height="14" viewBox="0 0 10 14"><path d="M5 0a5 5 0 0 0-5 5c0 4 5 9 5 9s5-5 5-9a5 5 0 0 0-5-5zm0 7a2 2 0 1 1 0-4 2 2 0 0 1 0 4z" fill="#fff"/></svg><span>4410 Cedar Pass Road<br>Brookfield, North America</span></li>
    <li><svg width="12" height="12" viewBox="0 0 24 24"><path fill="#fff" d="M6.6 10.8a15 15 0 0 0 6.6 6.6l2.2-2.2c.3-.3.7-.4 1-.2 1.1.4 2.3.6 3.6.6.6 0 1 .4 1 1V20c0 .6-.4 1-1 1A17 17 0 0 1 3 4c0-.6.4-1 1-1h3.5c.6 0 1 .4 1 1 0 1.3.2 2.5.6 3.6.1.3 0 .7-.2 1z"/></svg><span>555-014-2290</span></li>
    <li><svg width="12" height="10" viewBox="0 0 12 10"><rect x="0" y="0" width="12" height="10" fill="#fff"/><path d="M0 0l6 5 6-5" stroke="#222224" fill="none"/></svg><span>info@ridgelinehaul.com</span></li>
  </ul>
  <div class="map" role="img" aria-label="Location map with a red pin"></div>
  <div class="footer-bar">
    <span class="copyright">Copyright © 2019 Ridgeline Haul Carriers.All Rights Reserved.</span>
    <div class="social"><span></span><span></span><span></span></div>
  </div>
</footer>

</body>
</html>
```